Selfpublisher sucht Buch-Cover für Roman (Thriller)
Zielgruppe
Ich bin Selfpublisher und möchte meinen dritten Roman veröffentlichen. Ich suche ein hochwertiges Cover, das im Buchhandel direkt ins Auge sticht.
Zielgruppe: junge Erwachsene/Erwachsene, Genre Thriller
Aufgabenstellung
Für meinen neuer Thriller „STILLE KAMMER“ suche ich ein aussagekräftiges Cover.
Es sollte den Inhalt des Buches widerspiegeln, den ich nachfolgend so gut es geht erläutere.
Klappentext:
Nie wieder Gewalt, Hass und Schmerz. Das schwor sich Larissa, als sie vor zwei Jahren aus ihrer lieblosen Ehe flüchtete und im Hamburger Frauenhaus ein sicheres Zuhause fand. Nun fühlt sie sich bereit, endlich wieder auf eigenen Füßen zu stehen. Doch während sie sich Stück für Stück zurück ins Leben kämpft, ahnt sie nichts von der Gefahr, die ganz in ihrer Nähe lauert.
Er beobachtet sie.
Er kennt jeden ihrer Schritte.
Er sammelt.
Und Stille Kammer wird mit Abstand sein größter Clou.
Ein Mörder. Ein Opfer. Ein Geheimnis, das beide für immer verbindet.
Weiterer Inhalt:
In der Geschichte kommt es zu blutigen Szenen, Kämpfen und Fluchtversuchen. Der Haupthandlungsort ist der Keller des Entführers. Das Cover sollte mehrere Inhalte dieses Kellers sowie das Opfer abbilden, dafür bin ich für Vorschläge offen. Um diesen Keller besser verstehen zu können, beschreibe ich ihn grob:
- Boden und Wände aus Beton, alt und schmutzig, Wasserflecken
- Das Entführungsopfer ist hinter deckenhohen Gitterstäben gefangen, die den Zellenraum mittig teilen
- Das Opfer ist innerhalb dieser Zelle zusätzlich mit einer Kette versehen, die mit einem Ring am Hals und einer Öse in der Wand befestigt ist
- Im Zellenraum gibt es ein altes Bett mit Metallgestell sowie eine Toilette. Ein kleines Kellerfenster (vergittert), das sich über einem Heizkörper befindet, stellt den einzigen Bezug zur Außenwelt dar
Das Opfer:
- Junge Frau, 29 Jahre alt
- äußerst schlank
- blond
- trägt beigefarbene Gefangenenkleidung (schlichte Stoffhose, schlichtes Oberteil mit Knöpfen und kurzen Ärmeln, einfache Socken)
- ist festgekettet (Halsring aus Eisen, daran eine Kette, die ins Mauerwerk führt)

```html
<!DOCTYPE html>
<html lang="de">
<head>
<meta charset="utf-8">
<title>Stille Kammer – Buchumschlag</title>
<link href="https://fonts.googleapis.com/css2?family=Fjalla+One&family=Fira+Sans+Extra+Condensed:ital,wght@0,400;1,400&display=swap" rel="stylesheet">
<style>
  :root {
    --stage: #b4b4b4;
    --cover-top: #9a9ea8;
    --cover-mid: #5d6170;
    --cover-bottom: #1c1d26;
    --title-muted: #8f97a8;
    --title-bright: #f1f1f1;
    --text-light: #e6e7ea;
    --text-accent: #b3bac8;
  }
  * { margin: 0; padding: 0; box-sizing: border-box; }
  html, body { width: 848px; height: 1200px; overflow: hidden; }
  body {
    background: var(--stage);
    display: flex;
    align-items: center;
    justify-content: center;
    gap: 28px;
  }
  .cover {
    position: relative;
    width: 390px;
    height: 555px;
    overflow: hidden;
    border-radius: 2px;
  }
  .cover-art {
    position: absolute;
    inset: 0;
    width: 100%;
    height: 100%;
  }
  .front-title {
    position: absolute;
    left: 0; right: 0;
    top: 196px;
    text-align: center;
    font-family: "Fjalla One", sans-serif;
    font-size: 80px;
    line-height: 84px;
    letter-spacing: 0.5px;
  }
  .front-title .line-muted { display: block; color: var(--title-muted); }
  .front-title .line-bright { display: block; color: var(--title-bright); }
  .front-credit {
    position: absolute;
    left: 0; right: 0;
    top: 440px;
    text-align: center;
    font-family: "Fjalla One", sans-serif;
    font-size: 26px;
    line-height: 32px;
  }
  .front-credit .author { display: block; color: var(--title-bright); }
  .front-credit .genre { display: block; color: var(--text-accent); }
  .blurb {
    position: absolute;
    left: 40px;
    top: 34px;
    width: 300px;
    color: var(--text-light);
  }
  .blurb-head {
    font-family: "Fjalla One", sans-serif;
    font-size: 18px;
    line-height: 22px;
    color: var(--text-accent);
    margin-bottom: 6px;
  }
  .blurb-body p {
    font-family: "Fira Sans Extra Condensed", sans-serif;
    font-size: 13.2px;
    line-height: 22px;
    margin-bottom: 9px;
  }
  .blurb-body em { font-style: italic; }
  .blurb-tagline {
    margin-top: 18px;
    font-family: "Fjalla One", sans-serif;
    font-size: 18px;
    line-height: 28px;
    color: var(--text-accent);
  }
</style>
</head>
<body>
  <section class="cover cover-front">
    <svg class="cover-art" viewBox="0 0 390 555" role="img" aria-label="Unscharfe Silhouette einer Frau, die beide Hände gegen eine zerkratzte, beschlagene Glasscheibe drückt">
      <defs>
        <linearGradient id="frontShade" x1="0" y1="0" x2="0" y2="1">
          <stop offset="0" stop-color="var(--cover-top)"/>
          <stop offset="0.5" stop-color="var(--cover-mid)"/>
          <stop offset="1" stop-color="var(--cover-bottom)"/>
        </linearGradient>
      </defs>
      <rect width="390" height="555" fill="url(#frontShade)"/>
    </svg>
    <h1 class="front-title">
      <span class="line-muted">STILLE</span>
      <span class="line-bright">KAMMER</span>
    </h1>
    <p class="front-credit">
      <span class="author">HOLGER BRANDT</span>
      <span class="genre">THRILLER</span>
    </p>
  </section>

  <section class="cover cover-back">
    <svg class="cover-art" viewBox="0 0 390 555" role="img" aria-label="Unscharfe Hand, die von hinten gegen eine zerkratzte, beschlagene Glasscheibe drückt">
      <defs>
        <linearGradient id="backShade" x1="0" y1="0" x2="0" y2="1">
          <stop offset="0" stop-color="var(--cover-top)"/>
          <stop offset="0.5" stop-color="var(--cover-mid)"/>
          <stop offset="1" stop-color="var(--cover-bottom)"/>
        </linearGradient>
      </defs>
      <rect width="390" height="555" fill="url(#backShade)"/>
    </svg>
    <div class="blurb">
      <h2 class="blurb-head">NIE WIEDER GEWALT, HASS UND SCHMERZ.</h2>
      <div class="blurb-body">
        <p>Das schwor sich Larissa, als sie vor zwei Jahren aus ihrer lieblosen Ehe flüchtete und im Hamburger Frauenhaus ein sicheres Zuhause fand. Nun fühlt sie sich bereit, endlich wieder auf eigenen Füßen zu stehen. Doch während sie sich Stück für Stück zurück ins Leben kämpft, ahnt sie nichts von der Gefahr, die ganz in ihrer Nähe lauert.</p>
        <p>Er beobachtet sie.</p>
        <p>Er kennt jeden ihrer Schritte.</p>
        <p>Er <em>sammelt</em>.</p>
        <p>Und Stille Kammer wird mit Abstand<br>sein größter Clou.</p>
      </div>
      <p class="blurb-tagline">EIN MÖRDER. EIN OPFER.<br>EIN GEHEIMNIS, DAS BEIDE<br>FÜR IMMER VERBINDET.</p>
    </div>
  </section>
</body>
</html>
```